I want a website to be designed for our new company, it's an import and export company for variety of things.

please see the attached Logo for our company and the Images for our different sections for our busienss

Target Market(s)

multiple

Coding

Coded - Design and coding required

Number of Pages Required

5+ page

Font styles to use
Sans Serif

Colors

Designer to choose colors to be used in the design.

Requirements
Must have
• KVR GLOBALINKS
• KVR globalinks Trading & Contracting provides various services. The Company offers infrastructure construction, oil, enegy and gas services, agricultural projects, real estate development, travel and tourism, and food processing and trading.
• Civil contracting for infrastructure, residential and heavy projects. Through its main subsidiaries; distribution of general food products, construction chemicals including corrosion inhibitors and electrical machinery; provides catering and travel agency services; ownership and operation of a school; offers human sources services including manpower supply.
• Drilling and Gold Mines Used Machinery, All Kinds of Construction Machinery, Drilling Machines are manufactured and sold.
Nice to have
• good designa and beautiful colours, it has too look professional

```html
<!DOCTYPE html>
<html lang="en">
<head>
<meta charset="utf-8">
<title>KVR GLOBALINKS — Import &amp; Export</title>
<link href="https://fonts.googleapis.com/css2?family=Cinzel:wght@400;700&family=Open+Sans:wght@400;600;700&display=swap" rel="stylesheet">
<style>
:root{
  --bg:#1b1b1b;
  --header:#1c1c1c;
  --black:#000;
  --amber:#a35d17;
  --green-nav:#6fbf3c;
  --white:#fff;
  --muted:#d6d6d6;
  --panel:#2a2a2a;
  --oil:#1f1f1f;
  --energy:#7a2023;
  --agri:#3d5e28;
  --estate:#333;
  --travel:#25155e;
  --food:#121212;
  --accent-line:#3a2f8a;
  --quote:#5e5e5e;
  --contact:#2e2a2a;
}
*{box-sizing:border-box;margin:0;padding:0}
html,body{width:1200px;height:3869px;overflow:hidden}
body{background:var(--bg);color:var(--white);font-family:"Open Sans",sans-serif;position:relative}
.abs{position:absolute}
.serif{font-family:"Cinzel",serif}

/* header */
.site-header{left:0;top:0;width:1200px;height:132px;background:var(--header)}
.social{left:90px;top:46px;display:flex;gap:10px}
.ring{width:40px;height:40px;border:2px solid #e5e5e5;border-radius:50%;display:flex;align-items:center;justify-content:center}
.ring span{width:8px;height:8px;border-radius:50%;background:#e5e5e5}
.brand{left:450px;top:30px;width:300px;text-align:center}
.brand-mark{width:34px;height:34px;border:2px solid #cfcfcf;border-radius:50%;margin:0 auto 8px}
.brand-name{font-size:15px;letter-spacing:3px;font-weight:600;color:#e8e8e8}
.tools{left:790px;top:46px;display:flex;gap:14px}
.call{left:952px;top:42px;font-size:15px;line-height:1.3}
.call b{font-size:21px;font-weight:600;display:block}

.main-nav{left:0;top:132px;width:1200px;height:46px;background:var(--amber)}
.main-nav a{position:absolute;top:13px;font-size:15px;font-weight:600;color:var(--white);text-decoration:none}
.main-nav a.active{color:var(--green-nav)}

/* hero */
.hero{left:0;top:178px;width:1200px;height:513px;background:linear-gradient(180deg,#5b6058 0%,#6e6a60 35%,#565650 70%,#3a3a36 100%)}
.hero-band{left:0;top:661px;width:1200px;height:30px;background:var(--bg)}
.hero-title{left:0;top:318px;width:1200px;text-align:center;font-size:68px;font-weight:700;letter-spacing:1px;text-shadow:0 2px 6px rgba(0,0,0,.5)}
.hero-sub{left:0;top:396px;width:1200px;text-align:center;font-size:28px;font-weight:700;text-shadow:0 2px 6px rgba(0,0,0,.6)}
.btn{display:flex;align-items:center;justify-content:center;background:var(--amber);color:var(--white);border-radius:30px;font-weight:600;text-decoration:none}
.hero-btn{left:493px;top:475px;width:214px;height:54px;font-size:20px}

/* welcome */
.welcome-img{left:90px;top:811px;width:460px;height:415px;background:linear-gradient(135deg,#0e2a3d,#1d5a76 55%,#0b1b27)}
.address-card{left:412px;top:1133px;width:255px;height:219px;background:var(--panel);text-align:center;padding-top:28px;font-size:15.5px;line-height:28px;color:#e6e6e6}
.pin{width:50px;height:50px;border-radius:50%;background:#111;margin:0 auto 10px;display:flex;align-items:center;justify-content:center}
.welcome-title{left:601px;top:806px;font-size:40px;line-height:43px;font-weight:400}
.welcome-text{left:601px;top:908px;width:512px;font-size:15.5px;line-height:31.5px;color:var(--muted)}

/* offer */
.offer-title{left:0;top:1446px;width:1200px;text-align:center;font-size:44px;font-weight:400}
.tile{height:231px;padding:22px 12px}
.tile .icon{width:90px;height:90px;border-radius:50%;background:rgba(255,255,255,.12);display:flex;align-items:center;justify-content:center}
.tile h3{position:absolute;left:13px;top:128px;font-size:19px;font-weight:600}
.tile .arrow{position:absolute;left:13px;top:186px;font-size:18px}

/* services */
.block-black{background:var(--black)}
.svc-title{font-size:44px;line-height:49px;font-weight:700}
.svc-line{width:45px;height:3px;background:var(--accent-line)}
.svc-text{font-size:16.5px;line-height:32.5px;color:#e0e0e0;text-align:justify}
.svc-btn{width:161px;height:50px;font-size:16px;font-weight:700}

/* contact */
.map{left:0;top:3368px;width:1200px;height:501px;background:linear-gradient(180deg,#3d3d3d,#353535)}
.quote-box{left:107px;top:3244px;width:483px;height:244px;background:var(--quote);padding:22px 30px}
.quote-box h2{font-size:27px;line-height:36px;font-weight:700}
.quote-box p{margin-top:6px;font-size:14.5px;line-height:26px;color:#e2e2e2}
.quote-btn{margin-top:20px;width:209px;height:50px;background:#444;display:flex;align-items:center;justify-content:center;font-weight:700;font-size:16px}
.contact-box{left:608px;top:3244px;width:484px;height:244px;background:var(--contact);padding:26px 32px}
.contact-box h2{font-size:27px;font-weight:700;margin-bottom:8px}
.contact-row{display:flex;align-items:center;gap:16px;font-size:15.5px;height:36px}
.contact-row svg{width:18px}
.dots{display:flex;gap:30px;margin-top:16px}
.dots span{width:12px;height:12px;border-radius:50%;background:#e5e5e5}
.copy{left:0;top:3812px;width:1200px;text-align:center;font-size:13.5px;color:#eee}
</style>
</head>
<body>

<header class="abs site-header">
  <div class="abs social">
    <div class="ring" aria-label="Social profile"><span></span></div>
    <div class="ring" aria-label="Social profile"><span></span></div>
    <div class="ring" aria-label="Social profile"><span></span></div>
    <div class="ring" aria-label="Social profile"><span></span></div>
  </div>
  <div class="abs brand">
    <div class="brand-mark"></div>
    <div class="brand-name">KVR GLOBALINKS</div>
  </div>
  <div class="abs tools">
    <div class="ring"><svg width="16" height="16" viewBox="0 0 16 16" fill="#e5e5e5"><circle cx="8" cy="5" r="3.2"/><path d="M2 15c0-4 3-6 6-6s6 2 6 6z"/></svg></div>
    <div class="ring"><svg width="16" height="16" viewBox="0 0 16 16" fill="none" stroke="#e5e5e5" stroke-width="2"><circle cx="7" cy="7" r="4.5"/><path d="M10.5 10.5 14 14"/></svg></div>
    <div class="ring"><svg width="16" height="16" viewBox="0 0 24 24" fill="#e5e5e5"><path d="M6.6 10.8a15 15 0 0 0 6.6 6.6l2.2-2.2c.3-.3.7-.4 1-.2 1.1.4 2.3.6 3.6.6.6 0 1 .4 1 1V20c0 .6-.4 1-1 1A17 17 0 0 1 3 4c0-.6.4-1 1-1h3.5c.6 0 1 .4 1 1 0 1.3.2 2.5.6 3.6.1.3 0 .7-.2 1z"/></svg></div>
  </div>
  <div class="abs call">Call Us :<b>+8 000 123 456</b></div>
</header>

<nav class="abs main-nav">
  <a class="active" style="left:120px">HOME</a>
  <a style="left:224px">ABOUT US</a>
  <a style="left:357px">SERVICES</a>
  <a style="left:484px">RESOURCES</a>
  <a style="left:629px">BLOG</a>
  <a style="left:728px">PROJECTS</a>
  <a style="left:857px">GALLERY</a>
  <a style="left:981px">CONTACT US</a>
</nav>

<section class="abs hero" role="img" aria-label="Aerial view of a large hospital complex surrounded by roads and fields"></section>
<div class="abs hero-band"></div>
<div class="abs hero-title serif">KVR GLOBALINKS</div>
<div class="abs hero-sub">We are an import and export company for a variety of things</div>
<a class="abs btn hero-btn">Get Started</a>

<!-- welcome -->
<div class="abs welcome-img" role="img" aria-label="Businessman's open hand beneath a glowing world map with connection lines"></div>
<div class="abs address-card">
  <div class="pin"><svg width="22" height="24" viewBox="0 0 24 26" fill="none" stroke="#fff" stroke-width="1.8"><path d="M12 24s-7-7.5-7-13a7 7 0 0 1 14 0c0 5.5-7 13-7 13z"/><circle cx="12" cy="11" r="2.5"/></svg></div>
  No. 14, Jalan Cempaka<br>7/2, Taman Seri<br>Harmoni, 47100<br>Puchong, Malaysia.
</div>
<h1 class="abs welcome-title serif">Welcome to <b>KVR<br>Globalinks</b></h1>
<p class="abs welcome-text">Lorem ipsum dolor sit amet, consectetur adipiscing elit, sed do emod tempor incididunt ut labore et dolore magna aliqua. Ut enim ad minim veniam, quis nostrud exercitation ullamco laboris nisi ut aliquip ex ea commodo consequat. Duis aute irure dolor in reprehenderit in volutate velit esse cillum dolore eu fugiat nulla pariatur.</p>

<!-- offer -->
<h2 class="abs offer-title serif">What <b>We Offer</b></h2>

<div class="abs tile" style="left:90px;top:1520px;width:254px;background:var(--amber)"><div class="icon"><svg width="44" height="44" viewBox="0 0 44 44" fill="none" stroke="#fff" stroke-width="1.6"><rect x="6" y="14" width="18" height="26"/><path d="M6 8h32M30 8v32M10 20h10M10 26h10M10 32h10"/></svg></div><h3>Construction</h3><span class="arrow">→</span></div>
<div class="abs tile" style="left:344px;top:1520px;width:255px;background:var(--oil)"><div class="icon"><svg width="44" height="44" viewBox="0 0 44 44" fill="none" stroke="#fff" stroke-width="1.6"><path d="M4 38h36M8 38V20h8v18M20 38V12h8v26M32 38V24h6v14"/></svg></div><h3>Oil Industry</h3><span class="arrow">→</span></div>
<div class="abs tile" style="left:599px;top:1520px;width:256px;background:var(--energy)"><div class="icon"><svg width="44" height="44" viewBox="0 0 44 44" fill="none" stroke="#fff" stroke-width="1.6"><path d="M6 38h32V22l-8 5v-5l-8 5V12h-8v26"/><circle cx="18" cy="8" r="3"/></svg></div><h3>Energy &amp; Gas</h3><span class="arrow">→</span></div>
<div class="abs tile" style="left:855px;top:1520px;width:255px;background:var(--agri)"><div class="icon"><svg width="44" height="44" viewBox="0 0 44 44" fill="none" stroke="#fff" stroke-width="1.6"><circle cx="12" cy="14" r="6"/><circle cx="22" cy="14" r="6"/><circle cx="32" cy="14" r="6"/><path d="M12 20v18M22 20v18M32 20v18M4 38h36"/></svg></div><h3>Agricultural Projects</h3><span class="arrow">→</span></div>

<div class="abs tile" style="left:90px;top:1750px;width:340px;background:var(--estate)"><div class="icon"><svg width="44" height="44" viewBox="0 0 44 44" fill="none" stroke="#fff" stroke-width="1.6"><circle cx="22" cy="22" r="14"/><path d="M14 24l8-7 8 7v8H14z"/></svg></div><h3>Real estate development</h3><span class="arrow">→</span></div>
<div class="abs tile" style="left:430px;top:1750px;width:339px;background:var(--travel)"><div class="icon"><svg width="44" height="44" viewBox="0 0 44 44" fill="none" stroke="#fff" stroke-width="1.6"><path d="M6 18a16 10 0 0 1 32 0zM22 18v20M8 38h28M12 28h8v6h-8zM26 28h8v6h-8z"/></svg></div><h3>Travel and tourism</h3><span class="arrow">→</span></div>
<div class="abs tile" style="left:769px;top:1750px;width:341px;background:var(--food)"><div class="icon"><svg width="44" height="44" viewBox="0 0 44 44" fill="none" stroke="#fff" stroke-width="1.6"><rect x="8" y="20" width="14" height="18" rx="2"/><path d="M10 20v-8h10v8M22 26l14-10"/></svg></div><h3>Food processing and trading</h3><span class="arrow">→</span></div>

<!-- trading -->
<div class="abs block-black" style="left:0;top:2088px;width:670px;height:518px"></div>
<div class="abs" style="left:581px;top:2173px;width:527px;height:433px;background:linear-gradient(180deg,#8a8f8e 0%,#3e5b61 40%,#1f3a40 100%)" role="img" aria-label="Offshore drilling rig with helipad standing in open sea"></div>
<h2 class="abs svc-title serif" style="left:87px;top:2150px">Trading<br>Serices</h2>
<div class="abs svc-line" style="left:90px;top:2271px"></div>
<p class="abs svc-text" style="left:90px;top:2300px;width:418px">Lorem ipsum dolor sit amet, consectetur adipiscing elit, sed do eiusmod tempor incididunt ut labore et dolore magna aliqua. Ut enim ad minim veniam, quis nostrud exercitation ullamco laboris nisi ut aliquip ex ea commodo consequat.</p>
<a class="abs btn svc-btn" style="left:90px;top:2493px">Read More</a>

<!-- contracting -->
<div class="abs block-black" style="left:529px;top:2606px;width:671px;height:521px"></div>
<div class="abs" style="left:92px;top:2609px;width:525px;height:433px;background:linear-gradient(135deg,#e8e6e2,#bdb7ae 55%,#8a857e)" role="img" aria-label="Two businesspeople shaking hands over a desk with a pen and document"></div>
<h2 class="abs svc-title serif" style="left:686px;top:2668px">Contracting<br>Services</h2>
<div class="abs svc-line" style="left:688px;top:2790px"></div>
<p class="abs svc-text" style="left:688px;top:2820px;width:418px">Lorem ipsum dolor sit amet, consectetur adipiscing elit, sed do eiusmod tempor incididunt ut labore et dolore magna aliqua. Ut enim ad minim veniam, quis nostrud exercitation ullamco laboris nisi ut aliquip ex ea commodo consequat.</p>
<a class="abs btn svc-btn" style="left:688px;top:3013px">Read More</a>

<!-- contact -->
<div class="abs map" role="img" aria-label="Street map of the office neighbourhood"></div>
<div class="abs quote-box">
  <h2>Request A No-obligation<br>Free Quotation</h2>
  <p>Lorem ipsum dolor sit amet, consectetur adipiscing elit,<br>sed do eiusmod tempor incididunt ut labore et dolore</p>
  <div class="quote-btn">Request A Quote</div>
</div>
<div class="abs contact-box">
  <h2>Contact Us</h2>
  <div class="contact-row"><svg viewBox="0 0 24 26" fill="#fff"><path d="M12 24s-7-7.5-7-13a7 7 0 0 1 14 0c0 5.5-7 13-7 13z"/></svg>27 Larkspur Road, East Varden WA 6012</div>
  <div class="contact-row"><svg viewBox="0 0 24 18" fill="#fff"><path d="M1 1h22v16H1z"/><path d="M1 1l11 9 11-9" stroke="#2e2a2a" stroke-width="2" fill="none"/></svg>hello@kvrglobalinks.com</div>
  <div class="contact-row"><svg viewBox="0 0 24 24" fill="#fff"><path d="M6.6 10.8a15 15 0 0 0 6.6 6.6l2.2-2.2c.3-.3.7-.4 1-.2 1.1.4 2.3.6 3.6.6.6 0 1 .4 1 1V20c0 .6-.4 1-1 1A17 17 0 0 1 3 4c0-.6.4-1 1-1h3.5c.6 0 1 .4 1 1 0 1.3.2 2.5.6 3.6.1.3 0 .7-.2 1z"/></svg>+ 61 8 6120 4471</div>
  <div class="dots"><span></span><span></span><span></span></div>
</div>
<div class="abs copy">© 2020 Copyrights. The Company name . All rights reserved</div>

</body>
</html>
```